Harborline Business Card Designs***

WE ARE A FULL SERVICE FACILITY. ALL KINDS OF CAR/ TRK, REPAIR. CUSTOM WHEELS & TIRES. BRAKES, MUFFLERS, SHOCK, STRUTS...BATTERIES, STARTERS, ATERNATORS, TUNE UPS (WE DO IT ALL) ESTABLISHED IN 2004, LOCALLY OWNED AND OPERATED.... I AM OPEN TO SUGGESTIONS AS WELL ON ANY IDEAS

Contact Information for Business Card

WE DO COMPLETE AUTO REPAIR AND WHEELS, TIRES AND ACCESSORIES AT OUR STORE. I NAME OF SHOP (HARBORLINE AUTOMOTIVE GROUP) WOULD LIKE OUR EMAIL ON IT (HARBORLINEAUTOGROUP@QUVIX.NET) PHONE NUMBER 567-302-GEAR (4327) BUSINESS HOURS MON- SAT 8-6 SNAPGRID LOGO WITH (@HARBORLINE_AUTO_WESTRIDGE) WEBSITE (KESTRELROADWORKS.NET)FRIENDLOOP LOGO W/ (FRIENDLOOP.NET/HARBORLINEAUTOMOTIVE) AN A+/ QCR LOGO (THE LITTLE TORCH)... MAYBE EVEN EST.2004 INSIDE OF A "POW SIGN" (UNLESS IT GETS TO CLUTTERED) AND ON THE BACK OF THE CARD MAYBE A FAINT PICTURE OF "SOMETHING" IN BACKGROUND BUT STILL BE ABLE TO SEE THE ESTIMATE WE WRITE ON THE BACK. I WOULD LIKE ON THE BACK, DOWN IN THE RIGHT HAND CORNER A SPOT FOR A DATE AND INT. WE ALSO EXCEPT: ORBA, TRUSTPLATE, KELMORE AND ZINCWAY

```html
<!DOCTYPE html>
<html lang="en">
<head>
<meta charset="utf-8">
<title>Harborline Automotive Group – Business Card</title>
<link rel="stylesheet" href="https://fonts.googleapis.com/css2?family=Roboto+Condensed:wght@400;500&display=swap">
<style>
  :root {
    --canvas: #e9e9e9;
    --card: #efefef;
    --ink: #111111;
    --hours-blue: #2e3f9a;
    --burst-blue: #1ab0ec;
    --muted: #c9c9c9;
    --rule: #222222;
  }
  * { box-sizing: border-box; margin: 0; padding: 0; }
  html, body { width: 1200px; height: 1200px; overflow: hidden; background: var(--canvas); }
  .stage { position: relative; width: 1200px; height: 1200px; }
  .card {
    position: absolute; left: 222px; width: 750px; height: 450px;
    background: var(--card); overflow: hidden;
    box-shadow: 0 8px 18px rgba(0,0,0,0.18);
  }
  .card--front { top: 100px; }
  .card--back { top: 630px; }
  .card__photo {
    position: absolute; inset: 0;
    background: radial-gradient(ellipse at 55% 30%, rgba(190,190,195,0.55), rgba(225,225,228,0.35) 55%, rgba(239,239,239,0) 80%),
                linear-gradient(160deg, #e2e2e4, #ececec 60%, #e6e3e3);
  }
  .card__content { position: absolute; inset: 0; font-family: "Roboto Condensed", sans-serif; }
  .rule {
    position: absolute; left: 30px; right: 10px; height: 3px;
    background: linear-gradient(90deg, rgba(34,34,34,0) 0%, var(--rule) 30%, #777 55%, var(--rule) 82%, rgba(34,34,34,0) 100%);
  }

  /* front */
  .client-mark {
    position: absolute; top: 60px; left: 0; right: 0;
    display: flex; justify-content: center; align-items: center; gap: 10px;
    font-weight: 500; font-size: 32px; line-height: 1; color: var(--ink);
  }
  .client-mark__dot { width: 32px; height: 32px; border-radius: 50%; background: var(--ink); }
  .wordmark {
    position: absolute; left: 0; right: 0; text-align: center;
    font-weight: 500; color: var(--ink); line-height: 1; white-space: nowrap;
  }
  .card--front .wordmark { top: 165px; font-size: 44px; letter-spacing: 1px; }
  .hours {
    position: absolute; top: 230px; left: 0; right: 0; text-align: center;
    font-size: 21px; line-height: 1; color: var(--hours-blue);
  }
  .card--front .rule { top: 292px; }
  .contact-row {
    position: absolute; left: 0; right: 0; display: flex; justify-content: center; align-items: center;
    font-size: 16px; color: var(--ink);
  }
  .contact-row--primary { top: 318px; }
  .contact-row--social { top: 372px; }
  .contact-item { display: flex; align-items: center; gap: 6px; padding: 0 11px; height: 42px; }
  .contact-item + .contact-item { border-left: 1.5px solid #555; }
  .contact-item svg { flex: none; }
  .icon-square { width: 24px; height: 24px; border-radius: 4px; flex: none; }
  .icon-square--snap { background: #6b5a4a; }
  .icon-square--loop { background: #3d5f9e; }
  .badge-shape { width: 34px; height: 38px; background: #8fb0a8; border-radius: 3px; }

  /* back */
  .card--back .client-mark { top: 150px; left: 160px; right: auto; width: 340px; font-size: 20px; gap: 6px; }
  .card--back .client-mark__dot { width: 20px; height: 20px; }
  .card--back .wordmark { top: 200px; left: 160px; right: auto; width: 340px; font-size: 24px; }
  .est-burst { position: absolute; left: 540px; top: 150px; width: 160px; height: 120px; }
  .card--back .rule { top: 325px; }
  .payments { position: absolute; left: 85px; top: 345px; display: flex; align-items: center; gap: 8px; }
  .pay-mark {
    display: flex; align-items: center; gap: 5px; padding: 0 7px; height: 42px;
    font-weight: 500; font-size: 14px; color: var(--ink); background: #ffffff;
  }
  .pay-mark__chip { width: 12px; height: 12px; flex: none; }
  .pay-mark--zinc { background: transparent; padding: 0; }
  .pay-mark--zinc .pay-mark__chip { width: 30px; height: 30px; border-radius: 50%; background: #e0b640; }
  .estimate-fields { position: absolute; left: 531px; top: 346px; font-size: 17px; color: var(--ink); line-height: 21px; }
  .estimate-fields__hint { color: var(--muted); }
</style>
</head>
<body>
<main class="stage">

  <section class="card card--front">
    <div class="card__photo" role="img" aria-label="Faint photograph of a chrome engine bay with air cleaner"></div>
    <div class="card__content">
      <div class="client-mark"><span class="client-mark__dot"></span>Harborline</div>
      <div class="wordmark">HARBORLINE AUTOMOTIVE GROUP</div>
      <p class="hours">BUSINESS HOURS MON- SAT 8-6</p>
      <div class="rule"></div>

      <div class="contact-row contact-row--primary">
        <div class="contact-item">
          <svg width="24" height="24" viewBox="0 0 24 24" aria-hidden="true"><path d="M6.6 10.8c1.4 2.8 3.8 5.1 6.6 6.6l2.2-2.2c.3-.3.7-.4 1-.2 1.1.4 2.3.6 3.6.6.6 0 1 .4 1 1V20c0 .6-.4 1-1 1C10.6 21 3 13.4 3 4c0-.6.4-1 1-1h3.5c.6 0 1 .4 1 1 0 1.3.2 2.5.6 3.6.1.3 0 .7-.2 1z" fill="#111"/></svg>
          <span>567-302-GEAR (4327)</span>
        </div>
        <div class="contact-item">
          <svg width="26" height="26" viewBox="0 0 26 26" aria-hidden="true"><circle cx="13" cy="13" r="12" fill="none" stroke="#111" stroke-width="2"/><line x1="1" y1="13" x2="25" y2="13" stroke="#111" stroke-width="1.5"/><ellipse cx="13" cy="13" rx="5" ry="12" fill="none" stroke="#111" stroke-width="1.5"/></svg>
          <span>kestrelroadworks.net</span>
        </div>
        <div class="contact-item">
          <svg width="32" height="22" viewBox="0 0 32 22" aria-hidden="true"><rect x="1" y="1" width="30" height="20" fill="#111"/><path d="M1 1 L16 13 L31 1" fill="none" stroke="#efefef" stroke-width="2"/></svg>
          <span>harborlineautogroup@quvix.net</span>
        </div>
      </div>

      <div class="contact-row contact-row--social">
        <div class="contact-item"><span class="icon-square icon-square--snap"></span><span>@harborline_auto_westridge</span></div>
        <div class="contact-item"><span class="icon-square icon-square--loop"></span><span>harborlineautomotive</span></div>
        <div class="contact-item"><span class="badge-shape" role="img" aria-label="Accreditation badge"></span></div>
      </div>
    </div>
  </section>

  <section class="card card--back">
    <div class="card__photo" role="img" aria-label="Faint photograph of a chrome engine bay with air cleaner"></div>
    <div class="card__content">
      <div class="client-mark"><span class="client-mark__dot"></span>Harborline</div>
      <div class="wordmark">HARBORLINE AUTOMOTIVE GROUP</div>
      <svg class="est-burst" viewBox="0 0 160 120" aria-label="Established 2004">
        <polygon fill="var(--burst-blue)" points="98,3 102,30 140,18 124,44 158,58 122,70 132,100 102,84 92,118 76,88 52,108 52,82 18,88 36,66 2,56 36,44 22,20 56,30 68,4 80,28"/>
        <text x="80" y="68" text-anchor="middle" font-family="Roboto Condensed, sans-serif" font-size="23" fill="#ffffff">EST.2004</text>
      </svg>
      <div class="rule"></div>

      <div class="payments">
        <div class="pay-mark pay-mark--zinc"><span class="pay-mark__chip"></span>ZincWay</div>
        <div class="pay-mark"><span class="pay-mark__chip" style="background:#d8323a"></span>TrustPlate</div>
        <div class="pay-mark"><span class="pay-mark__chip" style="background:#1a3d8f"></span>Orba</div>
        <div class="pay-mark"><span class="pay-mark__chip" style="background:#e8782a"></span>Kelmore</div>
      </div>

      <div class="estimate-fields">
        <div>DATE : <span class="estimate-fields__hint">DD/MM/YYYY</span></div>
        <div>INT :</div>
      </div>
    </div>
  </section>

</main>
</body>
</html>
```